Business Card Design for Property Development Company Director

I am looking for a professional and unforgettable business card design for our Director of our Property Development Company.
Please see attached .pptx file to find out what information to include. You don't have to follow the exact format shown in the file - I am interested to see your creative flair using the information provided.

```html
<!DOCTYPE html>
<html lang="en">
<head>
<meta charset="utf-8">
<title>Norvale Property Group – Director Business Card</title>
<link rel="stylesheet" href="https://fonts.googleapis.com/css2?family=Lato:wght@400;700&display=swap">
<style>
  :root {
    --page-bg: #2b2c2e;
    --card-bg: #1c1d1f;
    --card-edge: #26272a;
    --brand-blue: #1f6fd1;
    --brand-grey: #6a6c70;
    --text-light: #f2f2f2;
    --text-soft: #c9cacc;
    --rule: #6a6c70;
    --pattern-top: #232427;
    --pattern-bottom: #1c1d1f;
  }
  * { box-sizing: border-box; margin: 0; padding: 0; }
  html, body { width: 1200px; height: 1108px; overflow: hidden; }
  body {
    background: var(--page-bg);
    font-family: "Lato", sans-serif;
    color: var(--text-light);
    display: flex;
    align-items: center;
    justify-content: center;
    gap: 80px;
  }
  .card {
    width: 360px;
    height: 590px;
    background: var(--card-bg);
    border-radius: 22px;
    position: relative;
    overflow: hidden;
    box-shadow: 0 20px 40px rgba(0,0,0,0.45);
  }

  /* Front */
  .card-front { display: flex; flex-direction: column; align-items: center; }
  .brand-lockup {
    margin-top: 120px;
    display: flex;
    align-items: center;
    gap: 14px;
  }
  .brand-square { width: 40px; height: 40px; background: var(--brand-blue); }
  .brand-name {
    font-weight: 700;
    font-size: 30px;
    letter-spacing: 1px;
    color: var(--brand-blue);
    line-height: 1.05;
    text-transform: uppercase;
  }
  .brand-name small { display: block; font-size: 13px; letter-spacing: 4px; }
  .person { margin-top: 120px; text-align: center; }
  .person-name {
    font-size: 24px;
    font-weight: 400;
    color: var(--brand-blue);
    text-transform: uppercase;
  }
  .person-role { font-size: 18px; color: var(--text-light); margin-top: 2px; }
  .icon-rule {
    display: flex; align-items: center; gap: 6px;
    width: 200px; margin-top: 10px;
  }
  .icon-rule .line { flex: 1; height: 1px; background: var(--rule); }
  .icon-rule svg { width: 24px; height: 24px; }
  .contact { text-align: center; margin-top: 10px; font-size: 18px; line-height: 1.35; }
  .contact-rule { width: 200px; height: 1px; background: var(--rule); margin-top: 16px; }
  .licence { margin-top: 14px; font-size: 18px; }
  .licence .label { color: var(--brand-blue); margin-right: 6px; }

  /* Back */
  .monogram-field {
    position: absolute; left: 0; top: 0; width: 100%; height: 64%;
    background: linear-gradient(180deg, var(--pattern-top), var(--pattern-bottom));
  }
  .back-content {
    position: absolute; left: 0; right: 0; bottom: 60px;
    display: flex; flex-direction: column; align-items: center; text-align: center;
  }
  .back-mark { display: flex; align-items: center; gap: 8px; margin-bottom: 22px; }
  .back-mark .brand-square { width: 22px; height: 22px; }
  .back-mark span { font-weight: 700; font-size: 18px; color: var(--brand-blue); letter-spacing: 1px; }
  .specialism { font-size: 19px; line-height: 1.3; text-transform: uppercase; color: var(--text-light); }
  .back-rule { width: 230px; height: 1px; background: var(--rule); margin: 16px 0 14px; }
  .invite { font-size: 16px; line-height: 1.3; color: var(--text-soft); }
</style>
</head>
<body>
  <article class="card card-front">
    <div class="brand-lockup">
      <div class="brand-square"></div>
      <div class="brand-name">Norvale<small>Property Group</small></div>
    </div>
    <div class="person">
      <h1 class="person-name">Daniel Marsh</h1>
      <p class="person-role">Director</p>
    </div>
    <div class="icon-rule">
      <span class="line"></span>
      <svg viewBox="0 0 24 24" aria-label="Phone"><circle cx="12" cy="12" r="12" fill="var(--brand-blue)"/><path d="M8 6.5l2.2 0 .8 3-1.4 1a7 7 0 0 0 3.9 3.9l1-1.4 3 .8v2.2c0 .8-.7 1.4-1.5 1.3A10 10 0 0 1 6.7 8c-.1-.8.5-1.5 1.3-1.5z" fill="var(--card-bg)"/></svg>
      <svg viewBox="0 0 24 24" aria-label="Email"><circle cx="12" cy="12" r="12" fill="var(--brand-blue)"/><rect x="6" y="8" width="12" height="8.5" fill="var(--card-bg)"/><path d="M6 8l6 5 6-5" fill="none" stroke="var(--brand-blue)" stroke-width="1.2"/></svg>
      <svg viewBox="0 0 24 24" aria-label="Website"><circle cx="12" cy="12" r="12" fill="var(--brand-blue)"/><circle cx="12" cy="12" r="6" fill="none" stroke="var(--card-bg)" stroke-width="1.5"/><ellipse cx="12" cy="12" rx="2.6" ry="6" fill="none" stroke="var(--card-bg)" stroke-width="1.2"/><path d="M6 12h12" stroke="var(--card-bg)" stroke-width="1.2"/></svg>
      <span class="line"></span>
    </div>
    <div class="contact">
      <p>0400 218 365</p>
      <p>daniel@norvale.com.au</p>
      <p>www.norvale.com.au</p>
    </div>
    <div class="contact-rule"></div>
    <p class="licence"><span class="label">Real Estate Lic:</span>5172936 &amp; 5172937</p>
  </article>

  <article class="card card-back">
    <div class="monogram-field" role="img" aria-label="Faint repeating brand monogram pattern"></div>
    <div class="back-content">
      <div class="back-mark"><div class="brand-square"></div><span>NORVALE</span></div>
      <p class="specialism">Property Development<br>&amp; Site Acquisition Specialists</p>
      <div class="back-rule"></div>
      <p class="invite">Ask me about our INVESTMENT<br>&amp; PARTNERSHIP opportunities</p>
    </div>
  </article>
</body>
</html>
```